Corvana Tongue Works, LLC

We need a business card that includes information about our business and conveys a reliable business that provides document translation services and interpreters for a variety of corporate and individual clients. We want to come across as professional, reliable, yet approachable. It should include the following on one side:

ESL / ENL Language Classes, Private Lessons, and Online Tutors
PLEXA Training and Testing
Translating & Interpreting Services
Contact us about Over-the-Phone Interpreting in over 200 languages
24/7/365
www.corvanatongue.example

The other side should include (555) 481-3062

Rhoda Pelling, President
482 Garnet Ave., Ste. 219
Indianapolis, IN 40917

Please add USA as part of the address. Also, please add rmpelling@corvanatongueworks.example as the e-mail address. Thank you.

Target Market(s)

Business professionals, their families, the international community

Industry/Entity Type

Business

Contact Information for Business Card

24/7/365
www.corvanatongue.example

(555) 481-3062

Rhoda Pelling, President
482 Garnet Ave., Ste. 219
Indianapolis, IN 40917
USA

Font styles to use
Sans Serif

Colors

Designer to choose colors to be used in the design.

Requirements
Must have
• See project description
• e-mail address and web address
• Phone number
Nice to have
• a globe
• physical address
Should not have
• Should not have the same color scheme as other agencies in our market in Indiana unless it is blue and black. No purple or yellow.

```html
<!DOCTYPE html>
<html lang="en">
<head>
<meta charset="utf-8">
<title>Corvana Tongue Works, LLC — Business Card</title>
<link rel="stylesheet" href="https://fonts.googleapis.com/css2?family=Roboto:wght@400;500;700&display=swap">
<style>
  :root {
    --stage: #2a2a2a;
    --brand-blue: #2596d6;
    --ink: #141414;
    --paper: #ffffff;
    --ribbon: #c4c4c4;
    --ribbon-fold: #8e8e8e;
  }
  * { box-sizing: border-box; margin: 0; padding: 0; }
  html, body { width: 1200px; height: 900px; overflow: hidden; }
  body {
    background: var(--stage);
    font-family: "Roboto", Arial, sans-serif;
    color: var(--ink);
    position: relative;
  }
  .card {
    position: absolute;
    left: 250px;
    width: 700px;
    height: 400px;
    overflow: hidden;
    box-shadow: 0 10px 28px rgba(0,0,0,0.55);
  }
  /* Front */
  .card-front { top: 35px; background: var(--brand-blue); }
  .brand {
    position: absolute;
    display: flex;
    align-items: center;
    gap: 16px;
  }
  .brand-dot {
    border-radius: 50%;
    border: 6px solid var(--paper);
    flex: none;
  }
  .brand-name {
    font-weight: 500;
    line-height: 1.05;
    color: var(--ink);
  }
  .card-front .brand { left: 175px; top: 60px; }
  .card-front .brand-dot { width: 110px; height: 110px; }
  .card-front .brand-name { font-size: 34px; }
  .services {
    position: absolute;
    left: 0; right: 0; top: 225px;
    text-align: center;
    font-size: 15.5px;
    line-height: 1.3;
  }
  .front-web {
    position: absolute;
    left: 0; right: 0; top: 345px;
    text-align: center;
    font-size: 16px;
  }
  /* Back */
  .card-back { top: 465px; background: var(--paper); }
  .back-art { position: absolute; inset: 0; }
  .card-back .brand { left: 40px; top: 120px; }
  .card-back .brand-dot { width: 100px; height: 100px; border-color: var(--brand-blue); }
  .card-back .brand-name { font-size: 28px; }
  .holder {
    position: absolute;
    left: 395px; top: 38px; width: 295px;
    text-align: center;
  }
  .holder-name { font-size: 21px; font-weight: 700; }
  .holder-title { font-size: 13px; }
  .contact-list {
    position: absolute;
    left: 50px; top: 250px;
    list-style: none;
  }
  .contact-list li {
    display: flex; align-items: center; gap: 12px;
    font-size: 17px; height: 30px; margin-bottom: 3px;
  }
  .contact-icon {
    width: 26px; height: 26px;
    background: var(--brand-blue);
    display: flex; align-items: center; justify-content: center;
    flex: none;
  }
  .address {
    position: absolute;
    left: 485px; top: 250px; width: 210px;
    text-align: center;
    color: var(--paper);
    font-size: 16px;
    font-style: normal;
    line-height: 1.3;
  }
  .address svg { display: block; margin: 0 auto 8px; }
</style>
</head>
<body>

<section class="card card-front" aria-label="Card front">
  <div class="brand">
    <span class="brand-dot"></span>
    <span class="brand-name">Corvana<br>Tongue Works,<br>LLC</span>
  </div>
  <p class="services">
    ESL / ENL Language Classes, Private Lessons, and Online Tutors<br>
    PLEXA Training and Testing<br>
    Translating &amp; Interpreting Services<br>
    Contact us about Over-the-Phone Interpreting in over 200 languages<br>
    24/7/365
  </p>
  <p class="front-web">www.corvanatongue.example</p>
</section>

<section class="card card-back" aria-label="Card back">
  <svg class="back-art" width="700" height="400" viewBox="0 0 700 400" aria-hidden="true">
    <defs>
      <linearGradient id="edgeShade" x1="0" x2="1">
        <stop offset="0" stop-color="#000" stop-opacity="0"/>
        <stop offset="1" stop-color="#000" stop-opacity="0.12"/>
      </linearGradient>
    </defs>
    <polygon points="380,0 402,0 472,400 450,400" fill="url(#edgeShade)"/>
    <polygon class="panel-blue" points="400,0 700,0 700,400 470,400" fill="var(--brand-blue)"/>
    <polygon points="380,100 412,100 412,125" fill="var(--ribbon-fold)"/>
    <rect x="380" y="30" width="320" height="70" fill="var(--ribbon)"/>
  </svg>

  <div class="brand">
    <span class="brand-dot"></span>
    <span class="brand-name">Corvana<br>Tongue Works,<br>LLC</span>
  </div>

  <div class="holder">
    <p class="holder-name">Rhoda Pelling</p>
    <p class="holder-title">President</p>
  </div>

  <ul class="contact-list">
    <li>
      <span class="contact-icon">
        <svg width="16" height="16" viewBox="0 0 16 16" aria-hidden="true"><path d="M3 1l3 3-1.5 2c1 2 2.5 3.5 4.5 4.5L11 9l3 3-2 2.5C6.5 14 2 9.5 1 3z" fill="#fff"/></svg>
      </span>
      (555) 481-3062
    </li>
    <li>
      <span class="contact-icon">
        <svg width="16" height="16" viewBox="0 0 16 16" aria-hidden="true"><path d="M1 5c4-3 10-3 14 0v2h-3V5.5H4V7H1z" fill="#fff"/><rect x="3" y="8" width="10" height="6" rx="1" fill="#fff"/></svg>
      </span>
      (555) 207-1148
    </li>
    <li>
      <span class="contact-icon">
        <svg width="16" height="16" viewBox="0 0 16 16" aria-hidden="true"><rect x="1" y="3" width="14" height="10" fill="none" stroke="#fff" stroke-width="1.5"/><path d="M1 3l7 6 7-6" fill="none" stroke="#fff" stroke-width="1.5"/></svg>
      </span>
      rmpelling@corvanatongueworks.example
    </li>
    <li>
      <span class="contact-icon">
        <svg width="16" height="16" viewBox="0 0 16 16" aria-hidden="true"><circle cx="8" cy="8" r="6.5" fill="none" stroke="#fff" stroke-width="1.4"/><ellipse cx="8" cy="8" rx="3" ry="6.5" fill="none" stroke="#fff" stroke-width="1.2"/><path d="M1.5 8h13" stroke="#fff" stroke-width="1.2"/></svg>
      </span>
      www.corvanatongue.example
    </li>
  </ul>

  <address class="address">
    <svg width="16" height="20" viewBox="0 0 16 20" aria-hidden="true"><path d="M8 1a6 6 0 0 1 6 6c0 4.5-6 12-6 12S2 11.5 2 7a6 6 0 0 1 6-6z" fill="#fff"/><circle cx="8" cy="7" r="2.3" fill="var(--brand-blue)"/></svg>
    482 Garnet Ave., Ste. 219<br>
    Indianapolis, IN 40917<br>
    USA
  </address>
</section>

</body>
</html>
```